Business Card, A4 Letter Head and DL Envelope for Brandvelle

We are looking for a design for our Business Card, A4 Letter Head and DL Envelope.

Brandvelle is a distributor of promotional products. We specialize in a range of branded promotional products, these include pens, polo shirts, key rings, drink bottles, uniforms and bags to name a few. We are experts in marketing and assist companies in choosing the right promotional product for their needs. We will predominately be an online business where customers visit our website and browse our range of promotional products and branding options.

Our colours are black, red, white and grey.

Files must be supplied in eps, pdf and ai format.

Please display the following information:
Derek Halloway
Account Manager
Suite xxx, 212 Ferrow Lane Melbourne, Victoria 3000
Phone +61 3 5550 1827
Mobile +61 455 016 342
sales@brandvelle-example.com.au
www.brandvelle-example.com.au

```html
<!DOCTYPE html>
<html lang="en">
<head>
<meta charset="utf-8">
<title>Brandvelle Stationery</title>
<link rel="stylesheet" href="https://fonts.googleapis.com/css2?family=Saira:wght@400;600&display=swap">
<style>
  :root {
    --board: #717171;
    --board-light: #7c7c7c;
    --paper: #ffffff;
    --red: #d41f26;
    --red-deep: #bf1c22;
    --ink: #222222;
    --faint: #efefef;
    --shade: rgba(0,0,0,0.08);
  }
  * { margin: 0; padding: 0; box-sizing: border-box; }
  html, body { width: 1200px; height: 785px; overflow: hidden; }
  body {
    position: relative;
    background: radial-gradient(ellipse at 50% 45%, var(--board-light), var(--board));
    font-family: "Saira", sans-serif;
    color: var(--ink);
  }
  .sheet {
    position: absolute;
    background: var(--paper);
    box-shadow: 3px 4px 8px rgba(0,0,0,0.35);
  }
  .letterhead { left: 50px; top: 49px; width: 525px; height: 681px; }
  .cover { left: 628px; top: 49px; width: 528px; height: 678px; }

  .header-band { position: absolute; top: 13px; height: 34px; background: var(--red); }
  .header-band--left { left: 0; width: 162px; }
  .header-band--right { right: 0; width: 162px; }

  .brand {
    position: absolute; display: flex; align-items: center;
    font-weight: 600; color: var(--ink); white-space: nowrap;
  }
  .brand-dot { border-radius: 50%; background: var(--red); flex: none; }
  .letterhead .brand { left: 176px; top: 14px; gap: 9px; font-size: 18px; letter-spacing: 0.6px; }
  .letterhead .brand-dot { width: 28px; height: 28px; }

  .faint-disc {
    position: absolute; left: 346px; top: 448px; width: 154px; height: 154px;
    border-radius: 50%; background: var(--faint);
  }
  .faint-shadow {
    position: absolute; left: 360px; top: 612px; width: 130px; height: 14px;
    border-radius: 50%; background: radial-gradient(ellipse, var(--shade), transparent 70%);
  }

  .footer-rule { position: absolute; left: 0; right: 0; top: 647px; height: 2px; background: var(--red); }
  .contact {
    position: absolute; left: 0; right: 0; text-align: center;
    font-size: 7.5px; line-height: 11px; color: var(--ink); white-space: nowrap;
  }
  .letterhead .contact { top: 653px; }
  .cover .contact { top: 641px; }
  .sep { color: var(--red); padding: 0 4px; }

  .cover-top { position: absolute; left: 0; top: 0; width: 528px; height: 339px; display: block; }
  .cover .brand {
    left: 0; right: 0; top: 392px; flex-direction: column; gap: 20px;
    font-size: 48px; line-height: 1; letter-spacing: 3px;
  }
  .cover .brand-dot { width: 140px; height: 140px; }
  .cover-shadow {
    position: absolute; left: 194px; top: 540px; width: 140px; height: 14px;
    border-radius: 50%; background: radial-gradient(ellipse, rgba(0,0,0,0.18), transparent 70%);
  }
</style>
</head>
<body>
  <section class="sheet letterhead" aria-label="A4 letterhead">
    <div class="header-band header-band--left"></div>
    <div class="header-band header-band--right"></div>
    <div class="brand"><span class="brand-dot"></span>Brandvelle</div>
    <div class="faint-disc" aria-hidden="true"></div>
    <div class="faint-shadow" aria-hidden="true"></div>
    <div class="footer-rule"></div>
    <div class="contact">
      <p>www.brandvelle-example.com.au<span class="sep">|</span>Suite xxx, 212 Ferrow Lane, Melbourne, Victoria 3000</p>
      <p>Tel: +61 3 5550 1827<span class="sep">|</span>Mob: +61 455 016 342<span class="sep">|</span>e-mail : sales@brandvelle-example.com.au</p>
    </div>
  </section>

  <section class="sheet cover" aria-label="Folder cover">
    <svg class="cover-top" viewBox="0 0 528 339" preserveAspectRatio="none" aria-hidden="true">
      <rect width="528" height="339" fill="var(--red-deep)"/>
      <path d="M0 339 C 90 200, 260 90, 528 60 L528 339 Z" fill="var(--red)"/>
      <path d="M0 339 C 90 200, 260 90, 528 60" fill="none" stroke="#e0454a" stroke-opacity="0.35" stroke-width="1"/>
    </svg>
    <div class="cover-shadow" aria-hidden="true"></div>
    <div class="brand"><span class="brand-dot"></span>Brandvelle</div>
    <div class="contact">
      <p>www.brandvelle-example.com.au<span class="sep">|</span>Suite xxx, 212 Ferrow Lane, Melbourne, Victoria 3000</p>
      <p>Tel: +61 3 5550 1827<span class="sep">|</span>Mob: +61 455 016 342<span class="sep">|</span>e-mail : sales@brandvelle-example.com.au</p>
    </div>
  </section>
</body>
</html>
```